Business card design

I need my logo on this card, things I need the card to have on it
licensed and insured.
owner operators Milo & Trent Halvorsen
my phone number 5083716254
Disaster Recovery, Storm Damage Restoration, Proactive Disaster Plan Management, Roof Repair/Restoration Structural Repair and Reconstruction, Emergency Boarding and Tarping Service, Perimeter Fencing, Emergency Tree Removal,

```html
<!DOCTYPE html>
<html lang="en">
<head>
<meta charset="utf-8">
<title>Halvorsen's Construction – Business Card</title>
<link rel="stylesheet" href="https://fonts.googleapis.com/css2?family=Lato:wght@400;700;900&display=swap">
<style>
  :root {
    --stage: #2e2e30;
    --brand-blue: #1596e8;
    --card-white: #ffffff;
    --ink-grey: #555a60;
    --band-grey: #6f7177;
  }
  * { box-sizing: border-box; margin: 0; padding: 0; }
  html, body { width: 1200px; height: 875px; overflow: hidden; }
  body {
    background: var(--stage);
    font-family: "Lato", sans-serif;
    display: flex;
    align-items: center;
    justify-content: center;
    gap: 40px;
  }
  .card {
    position: relative;
    width: 540px;
    height: 310px;
    border-radius: 18px;
    overflow: hidden;
    display: flex;
    align-items: center;
    box-shadow: 0 18px 40px rgba(0,0,0,.45);
  }
  .card--back { background: var(--brand-blue); color: var(--card-white); }
  .card--front { background: var(--card-white); color: var(--ink-grey); }

  .brand {
    width: 230px;
    display: flex;
    flex-direction: column;
    align-items: center;
    gap: 10px;
    padding-left: 24px;
  }
  .brand__mark { width: 18px; height: 18px; background: currentColor; }
  .brand__name {
    font-weight: 700;
    font-size: 20px;
    line-height: 1.25;
    text-align: center;
    letter-spacing: .5px;
  }
  .card--back .brand { color: var(--card-white); }
  .card--front .brand { color: var(--brand-blue); }

  .divider {
    width: 1.5px;
    height: 150px;
    background: currentColor;
    margin: 0 24px 0 10px;
    flex-shrink: 0;
  }
  .card--back .divider { background: var(--card-white); }
  .card--front .divider { background: var(--brand-blue); }

  .services { list-style: none; }
  .services li {
    display: flex;
    align-items: center;
    gap: 7px;
    font-size: 12.5px;
    line-height: 1.62;
  }
  .services svg { width: 12px; height: 12px; flex-shrink: 0; }

  .contact { display: flex; flex-direction: column; margin-top: -30px; }
  .contact__names {
    color: var(--brand-blue);
    font-weight: 900;
    font-size: 24px;
    letter-spacing: .5px;
  }
  .contact__role { font-size: 15px; margin-bottom: 10px; }
  .contact__line {
    display: flex; align-items: center; gap: 8px;
    font-size: 13px; line-height: 1.6;
  }
  .contact__line svg { width: 12px; height: 12px; fill: var(--brand-blue); flex-shrink: 0; }
  .contact__note {
    color: var(--brand-blue);
    font-weight: 700;
    font-size: 15px;
    margin-top: 10px;
  }

  .band {
    position: absolute; left: 0; right: 0; bottom: 0;
    height: 16px; display: flex;
  }
  .band__blue { flex: 1; background: var(--brand-blue); }
  .band__grey { width: 110px; background: var(--band-grey); border-left: 4px solid var(--card-white); }
</style>
</head>
<body>

  <section class="card card--back" aria-label="Card back – services">
    <div class="brand">
      <span class="brand__mark"></span>
      <p class="brand__name">HALVORSEN'S<br>CONSTRUCTION L.L.C</p>
    </div>
    <span class="divider"></span>
    <ul class="services">
      <li><svg viewBox="0 0 12 12"><circle cx="6" cy="6" r="6" fill="#fff"/><path d="M3.3 6.2l1.8 1.8 3.6-3.7" stroke="#1596e8" stroke-width="1.6" fill="none"/></svg>Disaster Recovery</li>
      <li><svg viewBox="0 0 12 12"><circle cx="6" cy="6" r="6" fill="#fff"/><path d="M3.3 6.2l1.8 1.8 3.6-3.7" stroke="#1596e8" stroke-width="1.6" fill="none"/></svg>Storm Damage Restoration</li>
      <li><svg viewBox="0 0 12 12"><circle cx="6" cy="6" r="6" fill="#fff"/><path d="M3.3 6.2l1.8 1.8 3.6-3.7" stroke="#1596e8" stroke-width="1.6" fill="none"/></svg>Proactive Disaster Plan Management</li>
      <li><svg viewBox="0 0 12 12"><circle cx="6" cy="6" r="6" fill="#fff"/><path d="M3.3 6.2l1.8 1.8 3.6-3.7" stroke="#1596e8" stroke-width="1.6" fill="none"/></svg>Roof Repair / Restoration</li>
      <li><svg viewBox="0 0 12 12"><circle cx="6" cy="6" r="6" fill="#fff"/><path d="M3.3 6.2l1.8 1.8 3.6-3.7" stroke="#1596e8" stroke-width="1.6" fill="none"/></svg>Structural Repair &amp; Reconstruction</li>
      <li><svg viewBox="0 0 12 12"><circle cx="6" cy="6" r="6" fill="#fff"/><path d="M3.3 6.2l1.8 1.8 3.6-3.7" stroke="#1596e8" stroke-width="1.6" fill="none"/></svg>Emergency Boarding &amp; Tarping Service</li>
      <li><svg viewBox="0 0 12 12"><circle cx="6" cy="6" r="6" fill="#fff"/><path d="M3.3 6.2l1.8 1.8 3.6-3.7" stroke="#1596e8" stroke-width="1.6" fill="none"/></svg>Perimeter Fencing</li>
      <li><svg viewBox="0 0 12 12"><circle cx="6" cy="6" r="6" fill="#fff"/><path d="M3.3 6.2l1.8 1.8 3.6-3.7" stroke="#1596e8" stroke-width="1.6" fill="none"/></svg>Emergency Tree Removal</li>
    </ul>
  </section>

  <section class="card card--front" aria-label="Card front – contact">
    <div class="brand">
      <span class="brand__mark"></span>
      <p class="brand__name">HALVORSEN'S<br>CONSTRUCTION L.L.C</p>
    </div>
    <span class="divider"></span>
    <div class="contact">
      <p class="contact__names">MILO &amp; TRENT</p>
      <p class="contact__role">Owner Operators</p>
      <p class="contact__line"><svg viewBox="0 0 12 12"><path d="M2.5 1h2l1 2.6-1.3 1a6.5 6.5 0 0 0 3.2 3.2l1-1.3 2.6 1v2c0 .8-.7 1.5-1.5 1.5A9.5 9.5 0 0 1 1 2.5C1 1.7 1.7 1 2.5 1z"/></svg>(508) 371-6254</p>
      <p class="contact__line"><svg viewBox="0 0 12 12"><path d="M0 2.5h12v7H0z M0 2.5l6 4 6-4" fill="#1596e8" stroke="#fff" stroke-width=".9"/></svg>info@halvorsensbuild.com</p>
      <p class="contact__line"><svg viewBox="0 0 12 12"><circle cx="6" cy="6" r="5.5"/><path d="M.5 6h11M6 .5c-2.5 3-2.5 8 0 11M6 .5c2.5 3 2.5 8 0 11" stroke="#fff" stroke-width=".8" fill="none"/></svg>halvorsensbuild.com</p>
      <p class="contact__note">licensed &amp; insured</p>
    </div>
    <div class="band"><span class="band__blue"></span><span class="band__grey"></span></div>
  </section>

</body>
</html>
```